New Pump Website Design Needed

We need a homepage concept for a pump website rebuild.

The navigation at the top must be:
Home - About Us - Pump Stations - Pumps - Electrical - Drainage - Environmental - Accessories - Contact Us

The homepage should have the the following structure:
Logo
Navigation
Rotating Banner
Content + Picture of PDF Flipbook to download/ view
Featured Products (in one row - approx 4)
Footer

The footer must include:
Left side - navigation small.
"Copyright KelvoRun 2014. All Rights reserved"

Right side: "Website by Pixel Orchard Studio"

Content and imagery, and Logo can be taken from their existing website: tarnbrookvalves.co.nz

We have attached a copy of their New PDF - the new website design must reflect this (Use block colours/ different colours for the navigation items/ incorporate the footer image).

Industry/Entity Type

Electrical

Font styles to use
Sans Serif

Requirements
Must have
• Features from their brochure brought in (colour scheme and footer feature)
Should not have
• Any Social Media Icons

```html
<!DOCTYPE html>
<html lang="en">
<head>
<meta charset="utf-8">
<title>KelvoRun Pump Systems</title>
<link rel="stylesheet" href="https://fonts.googleapis.com/css2?family=Arimo:wght@400;700&family=Open+Sans:wght@400;600&family=Raleway:wght@600&family=Russo+One&family=Play&display=swap">
<style>
:root{
  --red:#b5000f;
  --red-dark:#7d0a0f;
  --red-text:#7a0a0a;
  --blue:#00a8e6;
  --blue-deep:#0a7fc4;
  --ink:#333;
  --grey-panel:#222;
  --page:#fff;
}
*{margin:0;padding:0;box-sizing:border-box}
html,body{width:1200px;height:1200px;overflow:hidden;background:#fff}
body{font-family:"Arimo",Arial,sans-serif;color:var(--ink);position:relative}
.page{position:absolute;left:92px;top:0;width:1013px;height:1200px;background:var(--page);box-shadow:0 0 4px rgba(0,0,0,.25)}
.abs{position:absolute}

/* header */
.brand{left:72px;top:38px;display:flex;align-items:center;gap:10px;font-weight:700;font-size:30px;color:var(--red);letter-spacing:.5px}
.brand-mark{width:22px;height:22px;background:var(--blue-deep)}
.brand small{display:block;font-size:14px;letter-spacing:2px}
.search-label{left:732px;top:38px;font-size:12px;font-weight:700;color:var(--blue)}
.search-box{left:783px;top:30px;width:212px;height:29px;border:1px solid #ccc;border-radius:15px;background:linear-gradient(#f7f7f7,#ececec)}
.search-box svg{position:absolute;right:12px;top:6px}
.nav{left:300px;top:78px;width:713px;height:42px;background:var(--red);clip-path:polygon(22px 0,100% 0,100% 100%,0 100%)}
.nav ul{list-style:none;display:flex;align-items:center;height:100%;padding-left:34px;color:#fff;font-size:12.5px;white-space:nowrap}
.nav li+li::before{content:"|";margin:0 8px}
.rule{left:0;top:118px;width:1013px;height:7px;background:var(--red-dark)}

/* banner */
.banner{left:0;top:125px;width:1013px;height:421px;background:radial-gradient(ellipse at 50% 40%,#6a6a6a,#3a3a3a 80%)}
.photo-frame{left:68px;top:38px;width:604px;height:382px;background:#111;padding:7px}
.photo{width:100%;height:100%;background:linear-gradient(160deg,#b9c6c9 0%,#7f9a55 30%,#5a6e3a 55%,#6a4a30 80%,#4b3422 100%)}
.flip{left:669px;top:28px;width:276px;height:393px;background:var(--grey-panel);border:5px solid #151515;padding:28px 0 0 19px}
.flip h2{font-family:"Russo One",sans-serif;font-weight:400;font-size:20px;color:#fff;margin-bottom:16px}
.flip h2 span{color:var(--blue)}
.flip ul{list-style:none;font-family:"Open Sans",sans-serif;font-size:10.5px;line-height:15px;color:#fff;width:195px}
.flip li{position:relative;padding-left:22px;margin-bottom:13px}
.flip li::before{content:"";position:absolute;left:4px;top:4px;border-left:5px solid #fff;border-top:4px solid transparent;border-bottom:4px solid transparent}
.btn-blue{display:inline-block;margin-left:7px;width:129px;height:24px;line-height:24px;text-align:center;background:var(--blue);color:#fff;font-size:13px;border-radius:2px}

/* welcome */
.welcome{left:70px;top:586px;width:886px}
.welcome h1{font-family:"Raleway",sans-serif;font-weight:600;font-size:19px;color:#222;margin-bottom:8px}
.welcome p{font-size:12.3px;line-height:20.3px;text-align:justify;padding-left:3px;color:#444}
.welcome b{color:var(--red-text)}

/* featured cards */
.card{top:748px;width:203px;height:237px;border:1px solid #ddd;background:linear-gradient(#fff,#eee)}
.card h3{height:30px;background:linear-gradient(#b20a12,#7c0509);color:#fff;font-family:"Play",sans-serif;font-weight:400;font-size:17px;text-align:center;line-height:30px;white-space:nowrap}
.card .pic{position:absolute;left:16px;top:46px;width:170px;height:80px}
.card p{position:absolute;left:10px;right:10px;top:140px;text-align:center;font-size:12px;line-height:17px;color:#333}
.card .more{position:absolute;left:43px;bottom:-12px;width:117px;height:31px;background:linear-gradient(#8a8a8a,#5d5d5d);color:#fff;font-size:17px;text-align:center;line-height:31px;border-radius:2px}
.pic-a{background:linear-gradient(120deg,#cfcfcf,#3a63b0 45%,#9fa3a8)}
.pic-b{background:linear-gradient(160deg,#7d7c74,#a7a59d 50%,#3a5aa0 70%,#b3b0a8)}
.pic-c{background:linear-gradient(170deg,#6e7a5c,#8b8a78 45%,#c9b34a 60%,#6c6a5c)}
.pic-d{background:linear-gradient(150deg,#9aa0a6,#5d6b7a 50%,#c0c4c8)}

/* footer */
.footer{left:0;top:1071px;width:1013px;height:129px}
.footer svg{position:absolute;left:0;top:0}
.foot-nav{left:35px;top:65px;color:#fff;font-size:13px;font-weight:700;display:flex}
.foot-nav span+span::before{content:"|";margin:0 8px}
.copy{left:35px;top:87px;color:#fff;font-size:11.5px}
.credit{right:55px;top:84px;color:#fff;font-size:11.5px}
</style>
</head>
<body>
<div class="page">
  <div class="abs brand"><span class="brand-mark"></span><div>KelvoRun<small>PUMP SYSTEMS</small></div></div>
  <div class="abs search-label">Search</div>
  <div class="abs search-box"><svg width="18" height="18" viewBox="0 0 18 18"><circle cx="7" cy="7" r="5" fill="none" stroke="#333" stroke-width="1.8"/><line x1="11" y1="11" x2="16" y2="16" stroke="#333" stroke-width="2.4"/></svg></div>
  <nav class="abs nav"><ul><li>Home</li><li>About Us</li><li>Pump Stations</li><li>Pumps</li><li>Electrical</li><li>Drainage</li><li>Environmental</li><li>Accessories</li><li>Contact Us</li></ul></nav>
  <div class="abs rule"></div>

  <section class="abs banner">
    <div class="abs photo-frame"><div class="photo" role="img" aria-label="Tracked loader digging a trench across a rural lawn"></div></div>
    <aside class="abs flip">
      <h2>View <span>ONLINE FLIPBOK</span></h2>
      <ul>
        <li>Cement &amp; Aggregate Consulting Adds a New E-Band Gigabit Radio</li>
        <li>Cement &amp; Aggregate Consulting-MPLS with its Veyra Microwave Radios</li>
        <li>Cement &amp; Aggregate Consulting-Veyra MX12 Microwave Radio</li>
        <li>Cement &amp; Aggregate Consulting a New VAR Program</li>
        <li>Cement &amp; Aggregate Consulting a New VAR Program</li>
        <li>Cement &amp; Aggregate Consulting a New VAR Program</li>
      </ul>
      <span class="btn-blue">Download Here</span>
    </aside>
  </section>

  <section class="abs welcome">
    <h1>WELCOME TO TARNBROOK PUMPS.</h1>
    <p><b>Simply dummy text of the printing and typesetting industry.</b> Lorem Ipsum has been the industry's standard dummy text ever since the 1500s, when an unknown printer took a galley of type and scrambled it to make a type specimen book. It has survived not only five centuries, but also the leap into electronic typesetting, remaining essentially unchanged. It was popularised in the 1960s with the release of Presswell sheets containing Lorem Ipsum passages, and more recently with desktop publishing software like Quillset Layout including versions of Lorem Ipsum.</p>
  </section>

  <article class="abs card" style="left:70px">
    <h3>Products &amp; Services</h3>
    <div class="pic pic-a" role="img" aria-label="Workers fitting large blue pipe valves in a pit"></div>
    <p>Discover our innovative and compre-hensive line of licensed microwave radios and full turnkey services.</p>
    <span class="more">Read More</span>
  </article>
  <article class="abs card" style="left:293px">
    <h3>Industries Products</h3>
    <div class="pic pic-b" role="img" aria-label="Technician assembling a long blue pump shaft outdoors"></div>
    <p>Discover our innovative and compre-hensive line of licensed microwave radios and full turnkey services.</p>
    <span class="more">Read More</span>
  </article>
  <article class="abs card" style="left:516px">
    <h3>Electrical</h3>
    <div class="pic pic-d" role="img" aria-label="Pump control panel and electrical switchgear"></div>
    <p>Discover our innovative and compre-hensive line of licensed microwave radios and full turnkey services.</p>
    <span class="more">Read More</span>
  </article>
  <article class="abs card" style="left:739px">
    <h3>Get Support</h3>
    <div class="pic pic-c" role="img" aria-label="Excavator and site crew working on a dirt site"></div>
    <p>Discover our innovative and compre-hensive line of licensed microwave radios and full turnkey services.</p>
    <span class="more">Read More</span>
  </article>

  <footer class="abs footer">
    <svg width="1013" height="129" viewBox="0 0 1013 129">
      <defs>
        <linearGradient id="sea" x1="0" y1="0" x2="0" y2="1"><stop offset="0" stop-color="#1b8fd6"/><stop offset="1" stop-color="#0aa4e4"/></linearGradient>
      </defs>
      <path d="M0 10 C200 -5 380 5 560 18 C760 32 900 25 1013 12 L1013 129 L0 129Z" fill="#c4141c"/>
      <path d="M0 30 C220 14 420 22 600 30 C780 38 900 30 1013 18 L1013 129 L0 129Z" fill="#e8e8ef"/>
      <path d="M0 38 C230 22 430 30 610 38 C790 46 910 36 1013 22 L1013 129 L0 129Z" fill="url(#sea)"/>
    </svg>
    <div class="abs foot-nav"><span>Home</span><span>Pump</span><span>Station</span><span>Pump</span><span>Electrical</span><span>Drainage</span><span>Environmental</span><span>Accessories</span></div>
    <div class="abs copy">Copyright KelvoRun 2014. All Rights reserved</div>
    <div class="abs credit">Website by Pixel Orchard Studio</div>
  </footer>
</div>
</body>
</html>
```